Heritage Hollow Business Cards

Require a business card design. <br/><br/>Needs to include logo (either round or long version) plus these details:<br/>Maya Torvell<br/>Heritage Hollow<br/>maya@kelvadtrading.com.au<br/>02 6481 7395<br/>PO Box Glenwarra NSW 2791<br/>www.heritagehollow.com.au<br/><br/>I need in an editable format so that I can create for multiple staff members. <br/><br/>

Target Market(s)

We are an online store selling renovation products to home owners are builders. Looking for a classic classy design.

Industry/Entity Type

Home And Garden

Contact Information for Business Card

Maya Torvell
Heritage Hollow
maya@kelvadtrading.com.au
02 6481 7395
PO Box Glenwarra NSW 2791
www.heritagehollow.com.au

Colors

Designer to choose colors to be used in the design.

Requirements
Must have
• Must include Logo.

```html
<!DOCTYPE html>
<html lang="en">
<head>
<meta charset="utf-8">
<title>Heritage Hollow Business Cards</title>
<link rel="stylesheet" href="https://fonts.googleapis.com/css2?family=Tinos:wght@700&family=Source+Sans+3:wght@400;600&display=swap">
<style>
  :root {
    --backdrop: #c8c9cb;
    --ink-black: #070708;
    --charcoal: #231f20;
    --paper: #ffffff;
    --sage: #5a7a6b;
    --logo-ink: #231f20;
    --ring: #6b6b6b;
  }
  * { margin: 0; padding: 0; box-sizing: border-box; }
  html, body {
    width: 1139px;
    height: 1200px;
    overflow: hidden;
    background: var(--backdrop);
  }
  .card {
    position: absolute;
    left: 204px;
    width: 723px;
    height: 413px;
    border-radius: 14px;
    overflow: hidden;
  }
  .card--front { top: 169px; }
  .card--back { top: 620px; background: var(--ink-black); }
  .card__art {
    position: absolute;
    inset: 0;
    width: 723px;
    height: 413px;
  }
  .brand-seal {
    position: absolute;
    left: 82px;
    top: 22px;
    width: 228px;
    height: 228px;
    border: 1px solid var(--ring);
    border-radius: 50%;
  }
  .brand-name {
    position: absolute;
    left: 112px;
    top: 94px;
    width: 180px;
    font-family: "Source Sans 3", sans-serif;
    font-weight: 600;
    font-size: 36px;
    line-height: 36px;
    color: var(--logo-ink);
  }
  .holder {
    position: absolute;
    right: 30px;
    top: 32px;
    text-align: right;
    font-family: "Tinos", serif;
    font-weight: 700;
    color: var(--paper);
  }
  .holder__name { font-size: 31px; line-height: 34px; }
  .holder__role { font-size: 21px; line-height: 30px; }
  .address, .contacts {
    position: absolute;
    font-family: "Source Sans 3", sans-serif;
    font-weight: 400;
    font-size: 18px;
    line-height: 28px;
    color: var(--paper);
  }
  .address { left: 37px; top: 334px; }
  .contacts { right: 30px; top: 306px; text-align: right; }
  .contacts__line {
    display: flex;
    justify-content: flex-end;
    align-items: center;
    gap: 6px;
  }
  .contacts__icon { width: 14px; height: 14px; fill: none; stroke: var(--paper); }
  .back-seal {
    position: absolute;
    left: 89px;
    top: 104px;
    width: 192px;
    height: 192px;
    border: 1px solid var(--paper);
    border-radius: 50%;
  }
  .back-name {
    position: absolute;
    left: 100px;
    top: 216px;
    font-family: "Source Sans 3", sans-serif;
    font-weight: 600;
    font-size: 64px;
    line-height: 70px;
    color: var(--paper);
    white-space: nowrap;
  }
</style>
</head>
<body>

<section class="card card--front" aria-label="Business card front">
  <svg class="card__art" viewBox="0 0 1050 600" preserveAspectRatio="none" aria-hidden="true">
    <rect width="1050" height="600" fill="var(--ink-black)"/>
    <path d="M0,330 C170,470 400,470 620,415 S950,335 1050,350 L1050,600 L0,600 Z" fill="var(--charcoal)"/>
    <path d="M0,300 C160,445 400,440 620,385 S950,300 1050,318" fill="none" stroke="var(--sage)" stroke-width="14"/>
    <path d="M0,328 C170,468 400,468 620,413 S950,333 1050,348" fill="none" stroke="var(--paper)" stroke-width="3"/>
    <ellipse cx="290" cy="130" rx="372" ry="297" fill="none" stroke="var(--sage)" stroke-width="10"/>
    <ellipse cx="290" cy="130" rx="364" ry="290" fill="none" stroke="var(--paper)" stroke-width="3"/>
    <ellipse cx="290" cy="130" rx="356" ry="284" fill="var(--paper)"/>
  </svg>

  <div class="brand-seal"></div>
  <div class="brand-name">Heritage<br>Hollow</div>

  <div class="holder">
    <div class="holder__name">Maya Torvell</div>
    <div class="holder__role">Director</div>
  </div>

  <div class="address">PO Box Glenwarra<br>NSW 2791</div>

  <div class="contacts">
    <div class="contacts__line">
      <svg class="contacts__icon" viewBox="0 0 16 16" stroke-width="2"><path d="M3,2 L6,2 L7,5 L5,6.5 C6,9 7,10 9.5,11 L11,9 L14,10 L14,13 C8,14 2,8 3,2 Z" fill="var(--paper)" stroke="none"/></svg>
      <span>02 6481 7395</span>
    </div>
    <div class="contacts__line">
      <svg class="contacts__icon" viewBox="0 0 16 16" stroke-width="1.4"><rect x="1.5" y="3.5" width="13" height="9" fill="var(--paper)" stroke="none"/><path d="M1.5,3.5 L8,9 L14.5,3.5" stroke="var(--charcoal)"/></svg>
      <span>maya@kelvadtrading.com.au</span>
    </div>
    <div class="contacts__line">
      <svg class="contacts__icon" viewBox="0 0 16 16" stroke-width="1.2"><circle cx="8" cy="8" r="6.5"/><ellipse cx="8" cy="8" rx="3" ry="6.5"/><path d="M1.5,8 H14.5 M2.5,4.8 H13.5 M2.5,11.2 H13.5"/></svg>
      <span>www.heritagehollow.com.au</span>
    </div>
  </div>
</section>

<section class="card card--back" aria-label="Business card back">
  <div class="back-seal"></div>
  <div class="back-name">Heritage Hollow</div>
</section>

</body>
</html>
```